Brookvane Consulting Business Card Design

Business Card Design for Brookvane Consulting. Brookvane Consulting is a boutique consultancy based in Atlanta, GA., that specializes in marketing strategy, organization planning, and leadership development. We provide solutions for small businesses and startups as well as Vantage 300 companies.

http://brookvaneconsulting.com/

Target Market(s)

We provide solutions for small businesses and startups as well as Vantage 300 companies.

Industry/Entity Type

Consulting

Contact Information for Business Card

Two sided business card with priority on contact information, logo, tag line (Inspiration to Dream More, Do More, Become More)

Colors

Designer to choose colors to be used in the design.

Requirements
Must have
• contact information, logo, tag line (Inspiration to Dream More, Do More, Become More)
• Simple no over communication.
Nice to have
• I would like to see different placements of logo and creative use of both sides of the card
Should not have
• Do not put too much information on the card.

```html
<!DOCTYPE html>
<html lang="en">
<head>
<meta charset="utf-8">
<title>Brookvane Consulting Business Card</title>
<link rel="stylesheet" href="https://fonts.googleapis.com/css2?family=Roboto:wght@400;500&display=swap">
<style>
  :root {
    --backdrop: #555555;
    --card-dark: #3a3a3a;
    --card-light: #f1f1f1;
    --ink-dark: #2f2f2f;
    --ink-light: #f4f4f4;
    --brand-on-dark: #d9d9d9;
  }
  * { box-sizing: border-box; margin: 0; padding: 0; }
  html, body {
    width: 799px;
    height: 1200px;
    overflow: hidden;
    background: var(--backdrop);
    font-family: "Roboto", Arial, sans-serif;
  }
  .canvas {
    position: relative;
    width: 799px;
    height: 1200px;
  }
  .card {
    position: absolute;
    left: 90px;
    width: 620px;
    height: 354px;
    border-radius: 26px;
    overflow: hidden;
  }
  .card-front {
    top: 150px;
    background: var(--card-dark);
    display: flex;
    align-items: center;
    justify-content: center;
  }
  .card-back {
    top: 690px;
    background: var(--card-light);
  }
  .brand-name {
    font-weight: 500;
    letter-spacing: 0.5px;
    line-height: 1.1;
  }
  .card-front .brand-name {
    color: var(--brand-on-dark);
    font-size: 52px;
    text-align: center;
  }
  .wave {
    position: absolute;
    inset: 0;
    width: 100%;
    height: 100%;
  }
  .card-back .brand-name {
    position: absolute;
    left: 40px;
    top: 62px;
    color: var(--ink-dark);
    font-size: 36px;
  }
  .brand-line { display: block; }
  .tagline {
    position: absolute;
    right: 26px;
    top: 92px;
    width: 230px;
    color: var(--ink-light);
    font-size: 14px;
    line-height: 1.35;
    text-align: right;
  }
  .contact-list {
    position: absolute;
    left: 40px;
    top: 200px;
    list-style: none;
    color: var(--ink-dark);
    font-size: 14px;
    line-height: 1.55;
  }
  .holder-name {
    position: absolute;
    right: 36px;
    bottom: 28px;
    color: var(--ink-dark);
    font-size: 20px;
    font-weight: 500;
  }
</style>
</head>
<body>
<main class="canvas">
  <section class="card card-front" aria-label="Card front">
    <h1 class="brand-name">Brookvane Consulting</h1>
  </section>

  <section class="card card-back" aria-label="Card back">
    <svg class="wave" viewBox="0 0 620 354" preserveAspectRatio="none" aria-hidden="true">
      <path d="M230 0 C 380 40, 420 210, 620 235 L620 0 Z" fill="var(--ink-dark)"/>
      <path d="M170 0 C 350 30, 400 230, 620 262" fill="none" stroke="var(--ink-dark)" stroke-width="8"/>
      <path d="M120 0 C 330 20, 390 250, 620 282" fill="none" stroke="var(--ink-dark)" stroke-width="3"/>
    </svg>
    <h2 class="brand-name"><span class="brand-line">Brookvane</span><span class="brand-line">Consulting</span></h2>
    <p class="tagline">Inspiration to Dream More,<br>Do More, Become More</p>
    <ul class="contact-list">
      <li>555-014-2270</li>
      <li>dorian@brookvaneconsulting.com</li>
      <li>www.brookvaneconsulting.com</li>
    </ul>
    <p class="holder-name">Dorian</p>
  </section>
</main>
</body>
</html>
```